Luxury Business Card Design for High-End Window Treatments

Gilded Slatworks
Custom Plantation Shutters & Architectural Shading Systems

⸻

BACK

Daniel Trevick
Owner

Custom Interior & Exterior Window Treatments

919-555-0148
gildedslatworks.com

I have included a picture that I’m hoping we can use on the back, but I’m also wondering if you can get rid of the ladder? Should we get rid of shutters , shades and blinds underneath Gilded Slatworks?

Target Market(s)

High-end residential homeowners, custom home builders, architects, interior designers, and luxury renovation clients seeking premium plantation shutters and motorized architectural shading systems.

Industry/Entity Type

Custom Window treatments

Contact Information for Business Card

Front Gilded Slatworks Custom Plantation Shutters Motorized Architectural Shading Systems BACK Daniel Trevick Owner 919-555-0148 GildedSlatworks.com Custom Interior & Exterior Window Treatments By Appointment

Requirements
Nice to have
• Not 100% sure on nice to halves or the color but you can definitely check out my website to get a better understanding of what I’m trying to do

```html
<!DOCTYPE html>
<html lang="en">
<head>
<meta charset="utf-8">
<title>Gilded Slatworks — Business Card</title>
<link href="https://fonts.googleapis.com/css2?family=Lustria&family=Marcellus&display=swap" rel="stylesheet">
<style>
  :root {
    --backdrop: #6a6a6b;
    --card-black: #111111;
    --cream: #ece6d9;
    --gold-text: #f6d867;
    --gold-band: #fde46f;
    --white-text: #f2f2f2;
    --ink: #111111;
  }
  * { margin: 0; padding: 0; box-sizing: border-box; }
  html, body {
    width: 900px; height: 1200px; overflow: hidden;
    background: var(--backdrop);
  }
  .canvas { position: relative; width: 900px; height: 1200px; }
  .card {
    position: absolute; left: 135px; width: 630px; height: 358px;
    background: var(--card-black); overflow: hidden;
  }
  .card--front { top: 214px; }
  .card--back { top: 628px; }

  .photo-area {
    position: absolute; top: 0; right: 0; width: 345px; height: 100%;
    background:
      linear-gradient(180deg, #6f8fa8 0%, #3c4a58 22%, #2b3037 48%, #3a3d3c 70%, #2f3a2a 100%);
    -webkit-mask-image: linear-gradient(90deg, transparent 0%, #000 45%);
    mask-image: linear-gradient(90deg, transparent 0%, #000 45%);
  }

  .brand-name {
    position: absolute;
    font-family: "Marcellus", Georgia, serif;
    font-weight: 400;
    color: var(--cream);
    line-height: 1.02;
  }
  .card--front .brand-name { left: 45px; top: 92px; font-size: 50px; }
  .card--back .brand-name { left: 52px; top: 110px; font-size: 44px; }
  .brand-name .line-two { display: block; padding-left: 34px; }

  .services {
    position: absolute; display: flex;
    font-family: "Lustria", Georgia, serif;
    color: var(--gold-text);
  }
  .card--front .services { left: 43px; top: 250px; font-size: 24px; gap: 20px; }
  .card--back .services { left: 51px; top: 243px; font-size: 21px; gap: 18px; }

  .divider {
    position: absolute; left: 332px; top: 77px; width: 1.5px; height: 206px;
    background: var(--white-text);
  }
  .contact { position: absolute; left: 357px; top: 74px; font-family: "Lustria", Georgia, serif; color: var(--white-text); }
  .contact__name { font-size: 24px; color: var(--gold-text); line-height: 1.2; }
  .contact__role { font-size: 14px; letter-spacing: 1px; margin-top: 4px; }
  .contact__rule { width: 48px; height: 2px; background: var(--gold-text); margin-top: 6px; margin-bottom: 12px; }
  .contact__address { font-size: 14.5px; line-height: 25px; letter-spacing: 0.6px; }
  .contact__list { list-style: none; margin-top: 4px; font-size: 14.5px; letter-spacing: 1px; }
  .contact__list li { display: flex; align-items: center; gap: 7px; height: 24.5px; }
  .contact__list .phone-number { letter-spacing: 3px; font-size: 15px; }
  .contact__list svg { width: 12px; height: 12px; fill: var(--gold-text); flex: none; }

  .tagline-band {
    position: absolute; left: 0; top: 305px; width: 100%; height: 29px;
    background: var(--gold-band);
    font-family: "Lustria", Georgia, serif; font-size: 17px; color: var(--ink);
    display: flex; align-items: center; justify-content: center;
  }
</style>
</head>
<body>
<main class="canvas">

  <section class="card card--front">
    <div class="photo-area" role="img" aria-label="Photo of a two-storey home with a covered porch, white columns and exterior shades, trees and sky above"></div>
    <h1 class="brand-name">Gilded<span class="line-two">Slatworks</span></h1>
    <p class="services"><span>Shutters</span><span>Shades</span><span>Blinds</span></p>
  </section>

  <section class="card card--back">
    <h2 class="brand-name">Gilded<span class="line-two">Slatworks</span></h2>
    <p class="services"><span>Shutters</span><span>Shades</span><span>Blinds</span></p>
    <div class="divider"></div>
    <div class="contact">
      <p class="contact__name">Daniel Trevick</p>
      <p class="contact__role">Owner</p>
      <div class="contact__rule"></div>
      <p class="contact__address">418 Birch Ave<br>Suite 210 #3340<br>Fayetteville, NC 28305</p>
      <ul class="contact__list">
        <li><svg viewBox="0 0 24 24"><path d="M6.6 10.8a15.1 15.1 0 0 0 6.6 6.6l2.2-2.2a1 1 0 0 1 1-.25 11.4 11.4 0 0 0 3.6.57 1 1 0 0 1 1 1V20a1 1 0 0 1-1 1A17 17 0 0 1 3 4a1 1 0 0 1 1-1h3.5a1 1 0 0 1 1 1c0 1.25.2 2.45.57 3.57a1 1 0 0 1-.25 1z"/></svg><span class="phone-number">919-555-0148</span></li>
        <li><svg viewBox="0 0 24 24"><path d="M2 5h20v14H2z M2 5l10 8 10-8" stroke="#111" stroke-width="1.6"/></svg><span>info@gildedslatworks.com</span></li>
        <li><svg viewBox="0 0 24 24"><circle cx="12" cy="12" r="10"/><path d="M2 12h20M12 2c3 3 3 17 0 20M12 2c-3 3-3 17 0 20M4 7h16M4 17h16" stroke="#111" stroke-width="1.3" fill="none"/></svg><span>gildedslatworks.com</span></li>
      </ul>
    </div>
    <p class="tagline-band">Custom Interior &amp; Exterior Window Treatments By Appointment</p>
  </section>

</main>
</body>
</html>
```